Business Card Design Project

commercial exhaust hood cleaning and kitchen cleaning

Industry/Entity Type

Business

Contact Information for Business Card

a logo and name on front

```html
<!DOCTYPE html>
<html lang="en">
<head>
<meta charset="utf-8">
<title>Business Card – Front</title>
<link href="https://fonts.googleapis.com/css2?family=Open+Sans:ital,wght@0,400;0,600;0,800;1,400&display=swap" rel="stylesheet">
<style>
  :root {
    --bg: #e9e9eb;
    --card: #ffffff;
    --brand-blue: #1ea6e4;
    --blue-deep: #0b8fd3;
    --blue-light: #36b8f0;
    --stripe-gray: #55565a;
    --ink: #4a4a4d;
    --ink-soft: #5b5b5f;
  }
  * { box-sizing: border-box; margin: 0; padding: 0; }
  html, body {
    width: 1200px; height: 1000px; overflow: hidden;
    background: var(--bg);
    font-family: "Open Sans", Arial, sans-serif;
  }
  .business-card {
    position: absolute; left: 100px; top: 219px;
    width: 1000px; height: 562px;
    background: var(--card);
    box-shadow: 0 10px 30px rgba(0,0,0,.18);
    overflow: hidden;
  }
  .card-waves { position: absolute; inset: 0; width: 100%; height: 100%; }
  .company-name {
    position: absolute; left: 52px; top: 52px;
    font-weight: 800; font-size: 74px; line-height: 1;
    color: var(--brand-blue); letter-spacing: 1px;
  }
  .contact-block { position: absolute; left: 664px; top: 108px; color: var(--ink); }
  .person-name { font-style: italic; font-size: 38px; line-height: 1.1; color: var(--ink); }
  .person-role { font-size: 22px; color: var(--ink-soft); margin-top: 2px; }
  .address { font-size: 21px; line-height: 28px; margin-top: 38px; color: var(--ink-soft); }
  .contact-list { list-style: none; margin-top: 30px; }
  .contact-list li {
    display: flex; align-items: center; gap: 20px;
    font-size: 21px; line-height: 36px; color: var(--ink-soft);
  }
  .contact-icon { width: 22px; height: 22px; fill: var(--stripe-gray); flex: none; }
  .website {
    position: absolute; left: 64px; top: 496px;
    font-size: 22px; color: #ffffff; letter-spacing: .5px;
  }
</style>
</head>
<body>
  <main class="business-card">
    <svg class="card-waves" viewBox="0 0 1000 562" preserveAspectRatio="none" aria-hidden="true">
      <defs>
        <linearGradient id="blueBand" x1="0" y1="0" x2="0" y2="1">
          <stop offset="0" stop-color="var(--blue-light)"/>
          <stop offset="1" stop-color="var(--blue-deep)"/>
        </linearGradient>
      </defs>
      <path d="M0,286 C260,410 650,462 1000,432 L1000,464 C640,482 260,426 0,290 Z" fill="var(--stripe-gray)"/>
      <path d="M0,300 C260,440 640,500 1000,490 L1000,562 L0,562 Z" fill="url(#blueBand)"/>
    </svg>

    <div class="company-name">Logo Here</div>

    <section class="contact-block">
      <div class="person-name">Name Title</div>
      <div class="person-role">designation</div>
      <div class="address">suit # 00, Lorem ipsum<br>Lorem Lorem ipsum</div>
      <ul class="contact-list">
        <li>
          <svg class="contact-icon" viewBox="0 0 24 24"><rect x="1" y="1" width="22" height="22" rx="4"/><path d="M8 6c-1 1-1 3 1 6s4 5 6 5c1 0 2-1 2-2l-2-2-2 1c-1-1-2-2-3-4l1-2-2-2z" fill="#fff"/></svg>
          <span>000-000-0000</span>
        </li>
        <li>
          <svg class="contact-icon" viewBox="0 0 24 24"><rect x="6" y="2" width="12" height="7"/><rect x="2" y="9" width="20" height="10" rx="2"/><rect x="6" y="15" width="12" height="7" fill="#fff" stroke="var(--stripe-gray)" stroke-width="2"/></svg>
          <span>000-000-0000</span>
        </li>
        <li>
          <svg class="contact-icon" viewBox="0 0 24 24"><path d="M2 10 12 3l10 7v11H2z"/><path d="M4 11l8 6 8-6" fill="none" stroke="#fff" stroke-width="2"/></svg>
          <span>abcd@mailbox.example</span>
        </li>
      </ul>
    </section>

    <div class="website">www.abcdefg.example</div>
  </main>
</body>
</html>
```